Lumavento business card

We need a modern business card - With our 4 colors - See web: www.lumavento.dk

I have attached logo and som old business Cards we have - Lets Make the new ones shine...:-) -

Industry/Entity Type

Business

Requirements
Must have
• the logo with lumavento only,

```html
<!DOCTYPE html>
<html lang="da">
<head>
<meta charset="utf-8">
<title>Lumavento – visitkort</title>
<link rel="stylesheet" href="https://fonts.googleapis.com/css2?family=Open+Sans:wght@400;600;700&family=Questrial&display=swap">
<style>
  :root {
    --purple: #6b2a78;
    --magenta: #e0148c;
    --orange: #f28a1c;
    --lime: #9cc63a;
    --charcoal: #2b2b2b;
    --grey-text: #4a4a4a;
    --stage: #e9e6e1;
    --white: #ffffff;
  }
  * { box-sizing: border-box; margin: 0; padding: 0; }
  html, body {
    width: 1200px; height: 900px; overflow: hidden;
    background: var(--stage);
    font-family: "Open Sans", Arial, sans-serif;
  }
  .canvas {
    width: 1200px; height: 900px;
    display: flex; flex-direction: column; align-items: center; justify-content: center;
    gap: 34px;
  }
  .card {
    position: relative;
    width: 680px; height: 400px;
    overflow: hidden;
    box-shadow: 0 6px 18px rgba(0,0,0,.18);
  }

  /* Back side */
  .card--back { background: var(--charcoal); color: var(--white); }
  .back-brand {
    position: absolute; left: 0; right: 0; top: 120px;
    text-align: center;
    font-family: "Questrial", "Open Sans", sans-serif;
    font-size: 40px; letter-spacing: 6px; color: var(--white);
  }
  .back-rule { position: absolute; left: 170px; width: 340px; height: 2px; background: var(--white); }
  .back-rule--top { top: 205px; }
  .back-rule--bottom { top: 290px; }
  .back-name, .back-title {
    position: absolute; left: 0; right: 0; text-align: center;
    font-family: "Questrial", "Open Sans", sans-serif;
    letter-spacing: 3px; font-size: 20px;
  }
  .back-name { top: 218px; }
  .back-title { top: 250px; }

  /* Front side */
  .card--front { background: var(--white); }
  .front-graphics { position: absolute; inset: 0; }
  .holder { position: absolute; left: 70px; top: 30px; }
  .holder-name { font-size: 27px; font-weight: 700; color: var(--purple); line-height: 1.1; }
  .holder-name .first { color: var(--orange); }
  .holder-title { font-size: 15px; color: var(--purple); margin-top: 2px; }

  .contact { position: absolute; left: 100px; top: 140px; color: var(--purple); font-size: 19px; line-height: 1.3; }
  .contact-address { margin-left: 30px; margin-bottom: 2px; }
  .contact-row { display: flex; align-items: center; gap: 12px; }
  .contact-row svg { width: 18px; height: 18px; flex: none; }

  .brand { position: absolute; left: 420px; top: 170px; width: 230px; text-align: center; }
  .brand-name {
    display: flex; align-items: center; justify-content: center; gap: 10px;
    font-size: 28px; font-weight: 400; letter-spacing: 3px; color: var(--grey-text);
    padding-bottom: 10px; border-bottom: 2px solid var(--lime);
  }
  .brand-dot { width: 12px; height: 12px; border-radius: 50%; background: var(--lime); }
  .brand-tagline {
    font-size: 14px; color: var(--grey-text); margin-top: 10px;
    padding-bottom: 14px; border-bottom: 2px solid var(--lime);
  }
</style>
</head>
<body>
<main class="canvas">

  <section class="card card--back" aria-label="Visitkort bagside">
    <div class="back-brand">lumavento</div>
    <div class="back-rule back-rule--top"></div>
    <p class="back-name">Aksel Vinterberg</p>
    <p class="back-title">Salgsdirektør</p>
    <div class="back-rule back-rule--bottom"></div>
  </section>

  <section class="card card--front" aria-label="Visitkort forside">
    <svg class="front-graphics" viewBox="0 0 680 400" width="680" height="400" aria-hidden="true">
      <polygon points="0,28 52,28 30,62 0,62" fill="var(--magenta)"/>
      <polygon points="52,28 58,28 58,62 30,62" fill="var(--purple)"/>
      <polygon points="0,300 290,300 276,326 0,326" fill="var(--lime)"/>
      <polygon points="290,330 680,330 680,372 268,372" fill="var(--orange)"/>
    </svg>

    <header class="holder">
      <h1 class="holder-name"><span class="first">Aksel</span> Vinterberg</h1>
      <p class="holder-title">Salgsdirektør</p>
    </header>

    <address class="contact" style="font-style: normal;">
      <p class="contact-address">Solbakke Allé 14 - 2100<br>Østerbro - Tlf. 32 64 19 70</p>
      <p class="contact-row">
        <svg viewBox="0 0 24 24"><path fill="var(--orange)" d="M6.6 10.8a15 15 0 0 0 6.6 6.6l2.2-2.2a1 1 0 0 1 1-.25 11.4 11.4 0 0 0 3.6.57 1 1 0 0 1 1 1V20a1 1 0 0 1-1 1A17 17 0 0 1 3 4a1 1 0 0 1 1-1h3.5a1 1 0 0 1 1 1c0 1.25.2 2.45.57 3.57a1 1 0 0 1-.25 1z"/></svg>
        +45 41 27 63 08
      </p>
      <p class="contact-row">
        <svg viewBox="0 0 24 24"><rect x="2" y="5" width="20" height="14" rx="1.5" fill="var(--orange)"/><path d="M3 6l9 7 9-7" fill="none" stroke="var(--white)" stroke-width="1.6"/></svg>
        ak@lumavento.dk
      </p>
      <p class="contact-row">
        <svg viewBox="0 0 24 24"><circle cx="12" cy="12" r="10" fill="var(--orange)"/><path d="M2 12h20M12 2c3 3 3 17 0 20M12 2c-3 3-3 17 0 20" fill="none" stroke="var(--white)" stroke-width="1.4"/></svg>
        www.lumavento.dk
      </p>
    </address>

    <div class="brand">
      <div class="brand-name"><span class="brand-dot"></span>lumavento</div>
      <p class="brand-tagline">Medier til unge</p>
    </div>
  </section>

</main>
</body>
</html>
```